Business Card Design Project

I would like to have a project of business card with incorporated attachted logo elements in warm colors like: gold, yellow, brown.
We would like incorporate below information into the design
Name of the Company: Continental Ribbon Masters
Name: Darrell Finch
Position: Project Director
e-mail: darrell@ribbonmasters-demo.com
mobile: +65 83417729
website: www.ribbonmasters-demo.com
Address: 47 Marlow Road, #05-11, Singapore 417256
There is a picture attachted which can be used as a back side of the buisness card - we would like to follow the colors theme on the front card ( with the person contact details) how ever the front card we will prefer with white background but with graphfic elements coming from logo.
Reason: the project has been launched on 24 of April with deadline by 24 of April by mistakes. Thats why I would like to extend the deadline.
Name: Darrell Finch
mobile: +65 83417729

```html
<!DOCTYPE html>
<html lang="en">
<head>
<meta charset="utf-8">
<title>Continental Ribbon Masters – Business Card</title>
<link href="https://fonts.googleapis.com/css2?family=Dosis:wght@400;500;600&display=swap" rel="stylesheet">
<style>
  :root {
    --backdrop: #6e6e6e;
    --card-white: #ffffff;
    --card-mist: #ececec;
    --ink-purple: #5a2d82;
    --ink-grey: #8a8a8a;
    --ink-dark: #4a4a4a;
    --divider: #b5b5b5;
    --band-violet: #4b2a86;
    --band-magenta: #8a2a8e;
    --band-rose: #b0307f;
    --night: #050505;
    --night-glow: #2a1c10;
    --url-amber: #c9742a;
  }
  * { box-sizing: border-box; margin: 0; padding: 0; }
  html, body { width: 1200px; height: 431px; overflow: hidden; }
  body {
    background: var(--backdrop);
    position: relative;
    font-family: "Dosis", "Arial Narrow", sans-serif;
  }
  .card {
    position: absolute;
    top: 52px;
    width: 527px;
    height: 305px;
    overflow: hidden;
  }
  .card--front {
    left: 71px;
    background: linear-gradient(180deg, var(--card-mist) 0%, var(--card-white) 45%, var(--card-white) 100%);
  }
  .card--back {
    left: 624px;
    background: var(--night);
  }
  .brand {
    position: absolute;
    left: 32px;
    top: 96px;
    width: 190px;
    display: flex;
    align-items: center;
    gap: 10px;
  }
  .brand__dot {
    flex: none;
    width: 26px;
    height: 26px;
    border-radius: 50%;
    background: var(--ink-purple);
  }
  .brand__name {
    color: var(--ink-purple);
    font-weight: 600;
    font-size: 21px;
    line-height: 1.05;
    text-transform: uppercase;
    letter-spacing: 0.3px;
  }
  .divider {
    position: absolute;
    left: 234px;
    top: 68px;
    width: 1px;
    height: 70px;
    background: var(--divider);
  }
  .contact {
    position: absolute;
    left: 265px;
    top: 74px;
  }
  .contact__name {
    color: var(--ink-purple);
    font-weight: 500;
    font-size: 25px;
    line-height: 1;
  }
  .contact__role {
    color: var(--ink-grey);
    font-weight: 400;
    font-size: 20px;
    line-height: 1;
    margin-top: 6px;
    letter-spacing: 0.3px;
  }
  .contact__line {
    font-size: 16.5px;
    color: var(--ink-dark);
    line-height: 1;
    margin-top: 10px;
  }
  .contact__line:first-of-type { margin-top: 14px; }
  .contact__label { color: var(--ink-purple); font-weight: 600; }
  .swoosh {
    position: absolute;
    left: 0;
    bottom: 0;
    width: 527px;
    height: 60px;
    display: block;
  }
  .back-photo {
    position: absolute;
    inset: 0;
    background:
      radial-gradient(ellipse 150px 150px at 48% 48%, #4a3424 0%, var(--night-glow) 45%, transparent 100%),
      linear-gradient(90deg, var(--night) 0%, #140e08 50%, var(--night) 100%);
  }
  .back-url {
    position: absolute;
    right: 30px;
    bottom: 24px;
    color: var(--url-amber);
    font-size: 15px;
    font-weight: 400;
    letter-spacing: 0.2px;
  }
</style>
</head>
<body>
  <section class="card card--front">
    <div class="brand">
      <span class="brand__dot" aria-hidden="true"></span>
      <span class="brand__name">Continental<br>Ribbon<br>Masters</span>
    </div>
    <div class="divider" aria-hidden="true"></div>
    <div class="contact">
      <p class="contact__name">Darrell Finch</p>
      <p class="contact__role">Project Director</p>
      <p class="contact__line"><span class="contact__label">e-mail:</span> darrell@ribbonmasters-demo.com</p>
      <p class="contact__line"><span class="contact__label">mobile:</span> +65 83417729</p>
    </div>
    <svg class="swoosh" viewBox="0 0 527 60" preserveAspectRatio="none" aria-hidden="true">
      <defs>
        <linearGradient id="band-fill" x1="0" y1="0" x2="1" y2="0">
          <stop offset="0" stop-color="var(--band-magenta)"/>
          <stop offset="0.35" stop-color="var(--band-violet)"/>
          <stop offset="1" stop-color="var(--band-violet)"/>
        </linearGradient>
      </defs>
      <path d="M0 28 C 140 22, 300 4, 527 14 L 527 60 L 0 60 Z" fill="url(#band-fill)"/>
      <path d="M0 40 C 150 36, 300 22, 527 22" stroke="#ffffff" stroke-width="3" fill="none"/>
      <path d="M0 60 L 0 46 C 60 44, 120 42, 160 40 C 110 48, 80 54, 70 60 Z" fill="var(--band-rose)"/>
      <path d="M0 24 C 160 16, 320 0, 527 8" stroke="var(--band-violet)" stroke-width="1" fill="none"/>
    </svg>
  </section>

  <section class="card card--back">
    <div class="back-photo" role="img" aria-label="Photograph of a pole athlete performing a spin around a golden pole against a dark background"></div>
    <p class="back-url">www.ribbonmasters-demo.com</p>
  </section>
</body>
</html>
```